German Headhunter/ HR Consultancy needs Business Cards Design

We need a business Card Design for our Company in Stuttgart. We are specialized as Headhunter/ HR Consultancy in Placement of specialist and managers in permanent employment. Please refer to our business logo.

```html
<!DOCTYPE html>
<html lang="en">
<head>
<meta charset="utf-8">
<title>Kernwerk Personalberatung – Business Card</title>
<link href="https://fonts.googleapis.com/css2?family=Arimo:wght@400;700&display=swap" rel="stylesheet">
<style>
  :root {
    --page-bg: #e7e4df;
    --card-light: #f4ede2;
    --card-mid: #e6dccb;
    --card-warm: #d9ccb6;
    --navy: #1f3283;
    --navy-deep: #141f52;
    --band-blue: #2a47a5;
    --text-grey: #4d4a46;
    --rule: #55524e;
    --block-dark: #3b3129;
  }
  * { margin: 0; padding: 0; box-sizing: border-box; }
  html, body {
    width: 1200px;
    height: 927px;
    overflow: hidden;
    background: var(--page-bg);
    font-family: "Arimo", Arial, sans-serif;
  }
  .card {
    position: absolute;
    left: 50px;
    top: 156px;
    width: 1100px;
    height: 614px;
    background: linear-gradient(100deg, var(--card-light) 0%, #eef0f2 38%, var(--card-mid) 62%, var(--card-warm) 100%);
    box-shadow: 0 10px 30px rgba(0,0,0,0.18);
    overflow: hidden;
  }
  .brand {
    position: absolute;
    left: 93px;
    top: 70px;
    display: flex;
    align-items: center;
    gap: 22px;
  }
  .brand-square {
    width: 62px;
    height: 62px;
    background: var(--navy);
  }
  .brand-name {
    color: var(--navy);
    font-weight: 700;
    font-size: 34px;
    line-height: 1.15;
    letter-spacing: 1px;
    text-transform: uppercase;
  }
  .person {
    position: absolute;
    left: 93px;
    top: 250px;
  }
  .person-name {
    color: var(--navy);
    font-weight: 700;
    font-size: 40px;
    letter-spacing: 0.5px;
    line-height: 1;
  }
  .person-role {
    color: var(--text-grey);
    font-size: 28px;
    margin-top: 12px;
  }
  .contacts {
    position: absolute;
    left: 93px;
    top: 352px;
    list-style: none;
  }
  .contact-item {
    display: flex;
    align-items: center;
    gap: 16px;
    height: 43px;
    color: var(--text-grey);
    font-size: 27px;
  }
  .contact-icon { width: 26px; height: 26px; flex: none; }
  .divider {
    position: absolute;
    left: 93px;
    top: 491px;
    width: 761px;
    height: 2px;
    background: var(--rule);
  }
  .address {
    position: absolute;
    left: 93px;
    top: 506px;
    color: var(--text-grey);
    font-size: 27px;
  }
  .band-block {
    position: absolute;
    left: 0;
    bottom: 0;
    width: 79px;
    height: 30px;
    background: var(--block-dark);
  }
  .band-stripe {
    position: absolute;
    left: 93px;
    right: 0;
    bottom: 0;
    height: 30px;
    background: linear-gradient(90deg, var(--navy-deep) 0%, var(--navy) 45%, var(--band-blue) 62%, var(--navy-deep) 100%);
  }
</style>
</head>
<body>
  <div class="card">
    <div class="brand">
      <div class="brand-square"></div>
      <div class="brand-name">Kernwerk<br>Personalberatung</div>
    </div>

    <div class="person">
      <div class="person-name">JONATHAN SMITH</div>
      <div class="person-role">Manager</div>
    </div>

    <ul class="contacts">
      <li class="contact-item">
        <svg class="contact-icon" viewBox="0 0 24 24" aria-hidden="true">
          <path fill="#1f3283" d="M6.6 10.8c1.4 2.8 3.8 5.1 6.6 6.6l2.2-2.2c.3-.3.7-.4 1-.2 1.1.4 2.3.6 3.6.6.6 0 1 .4 1 1V20c0 .6-.4 1-1 1C10.6 21 3 13.4 3 4c0-.6.4-1 1-1h3.5c.6 0 1 .4 1 1 0 1.3.2 2.5.6 3.6.1.3 0 .7-.2 1z"/>
        </svg>
        123-456-2100
      </li>
      <li class="contact-item">
        <svg class="contact-icon" viewBox="0 0 24 24" aria-hidden="true">
          <rect x="2" y="5" width="20" height="14" fill="#1f3283"/>
          <path d="M2.5 5.5 12 13l9.5-7.5M2.5 18.5 9.5 11.5M21.5 18.5l-7-7" stroke="#f4ede2" stroke-width="1.4" fill="none"/>
        </svg>
        youremail@mailbox.com
      </li>
      <li class="contact-item">
        <svg class="contact-icon" viewBox="0 0 24 24" aria-hidden="true">
          <circle cx="12" cy="12" r="10" fill="#1f3283"/>
          <path d="M2 12h20M12 2c3 3 3 17 0 20M12 2c-3 3-3 17 0 20" stroke="#f4ede2" stroke-width="1.4" fill="none"/>
        </svg>
        www.yourwebsite.com
      </li>
    </ul>

    <div class="divider"></div>
    <div class="address">Your address, city, state, ZIP 0000</div>

    <div class="band-block"></div>
    <div class="band-stripe"></div>
  </div>
</body>
</html>
```